Business card for Crestline Bathrooms

Please design a business card for our bathroom renovation business. You can use my existing logo, but if you have an idea to modernize it, I would like to see it. Please see attached files first. I would like to use the blue and the orange theme. I like the concept of using the shower head in the logo. Please find following a design (or two) that I have been trying to create with my limited resources. That design was for a sign, but I was going to adopt it and use it as a business card as well. I like the concept of the water splash but I don’t think it “flows” nicely together with the logo. Another thought is that maybe creating the logo out of water splash could work and have a dramatic effect (like the water text and the butterfly picture attached with similar background instead of white). If the above doesn’t work I would like to see a modern simplified design. One of the attached files named as the unwanted business card has all the details that I want included in the business card. Please note that it is two sided.
Updates

I am very thankful for the designs that I have received, but they are very similar and only a couple of attempts to do something with the water splash as per my original brief. Modernizing the logo and having it made out of out of water splash with the orange as color accent could work and have a dramatic effect (like the water text and the butterfly picture attached with similar background instead of white). Please do not use the butterfly itself! This is just an example that images can be created out of water splash.

Contact Information for Business Card

all the details are on the unwonted business card file included

Colors
3176b5

Requirements
Nice to have
• Copied from the brief:
• ... maybe creating the logo out of water splash could work and have a dramatic effect (like the water text and the butterfly picture attached with similar background instead of white). Please do not use the butterfly itself!
Should not have
• I am getting designs with a butterfly. The butterfly picture was an example of creating something from a water splash. The butterfly itself has no association with anything other than the concept of creating a logo out of water splash. Sorry, I thought I was clear in the brief.

```html
<!DOCTYPE html>
<html lang="en">
<head>
<meta charset="utf-8">
<title>Crestline Bathrooms – Business Card</title>
<link rel="stylesheet" href="https://fonts.googleapis.com/css2?family=Roboto:wght@400;500;700&family=Gochi+Hand&display=swap">
<style>
  :root {
    --page: #e4e4e4;
    --navy: #182e50;
    --coral: #e8776a;
    --white: #ffffff;
    --mist: #c9d3e0;
  }
  * { box-sizing: border-box; margin: 0; padding: 0; }
  html, body { width: 1200px; height: 960px; overflow: hidden; }
  body {
    background: var(--page);
    font-family: "Roboto", Arial, sans-serif;
    color: var(--white);
    position: relative;
  }
  .card {
    position: absolute;
    width: 600px;
    height: 342px;
    background: var(--navy);
    overflow: hidden;
    box-shadow: 0 2px 4px rgba(0,0,0,.25);
  }
  .card--back { left: 302px; top: 124px; }
  .card--front { left: 299px; top: 493px; }

  .splash {
    position: absolute;
    top: 0;
    height: 100%;
    width: 320px;
  }
  .card--back .splash {
    left: 0;
    background:
      radial-gradient(ellipse 160px 28px at 120px 10px, rgba(201,211,224,.7), transparent 70%),
      radial-gradient(ellipse 70px 110px at 220px 200px, rgba(201,211,224,.35), transparent 70%),
      radial-gradient(ellipse 90px 70px at 70px 270px, rgba(201,211,224,.4), transparent 70%),
      radial-gradient(ellipse 120px 60px at 160px 320px, rgba(201,211,224,.35), transparent 70%);
  }
  .card--front .splash {
    right: 0;
    background:
      radial-gradient(ellipse 180px 30px at 190px 10px, rgba(201,211,224,.7), transparent 70%),
      radial-gradient(ellipse 70px 110px at 120px 190px, rgba(201,211,224,.35), transparent 70%),
      radial-gradient(ellipse 90px 70px at 250px 270px, rgba(201,211,224,.4), transparent 70%),
      radial-gradient(ellipse 120px 60px at 170px 320px, rgba(201,211,224,.35), transparent 70%);
  }

  .services {
    position: absolute;
    right: 42px;
    top: 61px;
    list-style: none;
    text-align: right;
    font-size: 15px;
    line-height: 24px;
  }
  .services li::after {
    content: "";
    display: inline-block;
    width: 6px; height: 6px;
    border-radius: 50%;
    background: var(--coral);
    margin-left: 7px;
    vertical-align: middle;
  }

  .badge { position: absolute; background: var(--white); }
  .badge--round { left: 378px; top: 262px; width: 32px; height: 32px; border-radius: 8px; }
  .badge--wide { left: 438px; top: 268px; width: 118px; height: 22px; border-radius: 2px; }

  .brand {
    position: absolute;
    left: 112px;
    top: 70px;
    display: flex;
    align-items: center;
    gap: 8px;
    font-size: 23px;
    font-weight: 500;
    color: var(--white);
  }
  .brand__dot { width: 12px; height: 12px; border-radius: 50%; background: var(--coral); }

  .person {
    position: absolute;
    left: 30px;
    top: 172px;
    font-family: "Gochi Hand", cursive;
    font-size: 23px;
    color: var(--coral);
    letter-spacing: .5px;
  }
  .contact {
    position: absolute;
    left: 31px;
    top: 208px;
    list-style: none;
    font-size: 16px;
    line-height: 21.5px;
  }
  .contact li { display: flex; align-items: center; gap: 7px; }
  .contact svg { width: 13px; height: 13px; fill: var(--coral); flex: none; }
  .contact__phones { font-weight: 700; font-size: 17.5px; }
  .contact__sep { font-weight: 400; margin: 0 10px; }
  .abn { position: absolute; left: 50px; top: 308px; font-size: 10px; }
</style>
</head>
<body>

<section class="card card--back">
  <div class="splash" role="img" aria-label="Water splash photograph in white and pale blue on navy"></div>
  <ul class="services">
    <li>Complete Bathroom Renovations &amp; Remodelling</li>
    <li>Professional Service From Concept To Completion</li>
    <li>Highly Skilled &amp; Qualified Tradespeople</li>
    <li>All Work Guaranteed</li>
  </ul>
  <div class="badge badge--round" role="img" aria-label="Industry association badge"></div>
  <div class="badge badge--wide" role="img" aria-label="Builders association badge"></div>
</section>

<section class="card card--front">
  <div class="splash" role="img" aria-label="Water splash photograph in white and pale blue on navy"></div>
  <div class="brand"><span class="brand__dot"></span>Crestline Bathrooms</div>
  <p class="person">Daniel Marsh</p>
  <ul class="contact">
    <li class="contact__phones">
      <svg viewBox="0 0 24 24"><path d="M6.6 10.8a15 15 0 0 0 6.6 6.6l2.2-2.2c.3-.3.7-.4 1-.2 1.1.4 2.3.6 3.6.6.6 0 1 .4 1 1V20c0 .6-.4 1-1 1A17 17 0 0 1 3 4c0-.6.4-1 1-1h3.5c.6 0 1 .4 1 1 0 1.3.2 2.5.6 3.6.1.3 0 .7-.2 1z"/></svg>
      0400 123 456<span class="contact__sep">|</span>6200 4100
    </li>
    <li>
      <svg viewBox="0 0 24 24"><path d="M12 2a10 10 0 1 0 5 18.7l-1-1.7A8 8 0 1 1 20 12v1.5a1.5 1.5 0 0 1-3 0V12a5 5 0 1 0-1.5 3.5A3.5 3.5 0 0 0 22 13.5V12A10 10 0 0 0 12 2zm0 13a3 3 0 1 1 0-6 3 3 0 0 1 0 6z"/></svg>
      daniel@crestlinebathrooms.com.au
    </li>
    <li>
      <svg viewBox="0 0 24 24"><path d="M12 2a10 10 0 1 0 0 20 10 10 0 0 0 0-20zm-1 17.9A8 8 0 0 1 4.2 10L9 15v1a2 2 0 0 0 2 2zm6.9-2.5A2 2 0 0 0 16 16h-1v-3a1 1 0 0 0-1-1H8v-2h2a1 1 0 0 0 1-1V7h2a2 2 0 0 0 2-2v-.4a8 8 0 0 1 2.9 12.8z"/></svg>
      crestlinebathrooms.com.au
    </li>
    <li>
      <svg viewBox="0 0 24 24"><path d="M2 5h20v14H2zm2 2v.5l8 5 8-5V7z"/></svg>
      PO Box 18 Eastvale 2600
    </li>
  </ul>
  <p class="abn">ABN 12 345 678 901</p>
</section>

</body>
</html>
```